New Property development signage

large poster for a new development.
3 metres x 2 metres. To include the following.

Tresswick Gardens
TO LET
LUXURY FULLY FURNISHED LARGE
2 AND 3 BED APARTMENTS
Garrold Estates
362 4150
www.garroldestates-example.com

Need this to be large simple writing with Garrold estates logo on the bottom

Target Market(s)

High end rental property market

Industry/Entity Type

Real Estate Development

Colors
000000
cbcbcb
0555a3

Requirements
Must have
• Name of the development must be in a different font, classic style
Nice to have
• Light Grey background, blues for colours
Should not have
• anymore than 3 /4 colours

```html
<!DOCTYPE html>
<html lang="en">
<head>
<meta charset="utf-8">
<title>To Let – Tresswick Gardens</title>
<link rel="stylesheet" href="https://fonts.googleapis.com/css2?family=Cinzel:wght@700&family=Jost:wght@600;700&display=swap">
<style>
  :root {
    --brand-blue: #28388a;
    --sign-white: #ffffff;
  }
  html, body {
    margin: 0;
    padding: 0;
    width: 800px;
    height: 1200px;
    overflow: hidden;
    background: var(--sign-white);
  }
  .sign {
    display: block;
    width: 800px;
    height: 1200px;
  }
  .headline-band { fill: var(--brand-blue); }
  .headline-text {
    fill: var(--sign-white);
    font-family: "Jost", "Century Gothic", sans-serif;
    font-weight: 600;
    font-size: 252px;
  }
  .info-line {
    fill: var(--brand-blue);
    font-family: "Jost", "Futura", sans-serif;
    font-weight: 700;
  }
  .development-name {
    fill: var(--brand-blue);
    font-family: "Cinzel", "Trajan Pro", serif;
    font-weight: 700;
    font-size: 58px;
  }
  .divider { fill: var(--brand-blue); }
  .agent-mark { fill: var(--brand-blue); }
  .agent-name {
    fill: var(--brand-blue);
    font-family: "Jost", "Futura", sans-serif;
    font-weight: 700;
    font-size: 42px;
  }
  .agent-web {
    fill: var(--brand-blue);
    font-family: "Jost", "Futura", sans-serif;
    font-weight: 600;
    font-size: 30px;
  }
</style>
</head>
<body>
<svg class="sign" viewBox="0 0 800 1200" xmlns="http://www.w3.org/2000/svg">
  <g class="headline">
    <rect class="headline-band" x="32" y="100" width="736" height="205"/>
    <text class="headline-text" x="100" y="285" textLength="600" lengthAdjust="spacingAndGlyphs">TOLET</text>
  </g>

  <g class="details">
    <text class="info-line" x="400" y="389" font-size="46" text-anchor="middle" textLength="736" lengthAdjust="spacingAndGlyphs">LUXURY FULLY FURNISHED LARGE</text>
    <rect class="divider" x="32" y="415" width="736" height="13"/>
    <text class="info-line" x="400" y="507" font-size="50" text-anchor="middle" textLength="736" lengthAdjust="spacingAndGlyphs">2 AND 3 BED APARTMENTS</text>
    <rect class="divider" x="32" y="543" width="736" height="12"/>
    <text class="development-name" x="400" y="640" text-anchor="middle" textLength="600" lengthAdjust="spacingAndGlyphs">Tresswick Gardens</text>
    <rect class="divider" x="32" y="681" width="736" height="13"/>
    <text class="info-line" x="400" y="777" font-size="60" text-anchor="middle" textLength="368" lengthAdjust="spacingAndGlyphs">PH: 362 4150</text>
  </g>

  <g class="agent">
    <rect class="agent-mark" x="33" y="958" width="56" height="56"/>
    <text class="agent-name" x="104" y="1001">Garrold Estates</text>
    <text class="agent-web" x="768" y="1054" text-anchor="end">www.garroldestates-example.com</text>
  </g>
</svg>
</body>
</html>
```